Business card design needed

I run a Beautician studio (for 7 years now)
I offer
- Velmo Body Sugaring
- Ruby Glaze
- Nails
- Facials
- Manicure
- Foot Treatment
It might not be necessary to list all those treatments?
Maybe the link to the Website is sufficient?
I leave that up to you ...
(more info on www.FernAndDewByLenka.com.au)
Velmo BodySugaring is our biggest success, It replaces waxing.
I would like to incorporate the logo into the Business Card.
We had many complaints regarding our old Business Cards as the Phone Number was to small.
On the backside, we would like a "your next Appointment" section.
Looking forward to you Design, cheers ... Lenka
Industry/Entity Type
Business
Contact Information for Business Card
Fern by Dew by Lenka
14 Korrin Sqr 3942 Talloway
www.FernAndDewByLenka.com.au
03 9481 2267

```html
<!DOCTYPE html>
<html lang="en">
<head>
<meta charset="utf-8">
<title>Velmo Body Sugaring – Business Card Set</title>
<link href="https://fonts.googleapis.com/css2?family=Arimo:wght@400;700&family=Open+Sans:wght@400;600;700&family=Cinzel:wght@500&display=swap" rel="stylesheet">
<style>
  :root{
    --backdrop:#1f1f21;
    --card:#ffffff;
    --ink:#1d1d1d;
    --grey:#555555;
    --line-grey:#8a8a8a;
    --green:#1f6b35;
    --green-bright:#129142;
    --orange:#e9572a;
    --amber:#f39a1f;
    --yellow:#f5c518;
    --faint:#f6f6f6;
  }
  *{box-sizing:border-box;margin:0;padding:0}
  html,body{width:1200px;height:728px;overflow:hidden;background:var(--backdrop)}
  .canvas{position:relative;width:1200px;height:728px}
  .card{position:absolute;width:542px;height:308px;background:var(--card);border-radius:22px;overflow:hidden;font-family:"Open Sans",sans-serif;color:var(--grey)}
  .card--front{left:41px;top:36px}
  .card--appt-a{left:615px;top:37px}
  .card--back{left:43px;top:380px}
  .card--appt-b{left:625px;top:383px}

  /* brand name block */
  .brand{display:flex;flex-direction:column;align-items:center;position:absolute}
  .brand__dot{width:62px;height:62px;border-radius:50%;background:linear-gradient(180deg,var(--amber),var(--orange))}
  .brand__name{margin-top:10px;font-family:"Open Sans",sans-serif;font-weight:600;color:var(--ink);text-align:center;letter-spacing:2px;text-transform:uppercase;line-height:1.25}

  /* front */
  .card--front .brand{left:66px;top:66px;width:180px}
  .card--front .brand__name{font-size:17px}
  .divider{position:absolute;left:270px;top:64px;width:1px;height:106px;background:linear-gradient(180deg,transparent,var(--line-grey),transparent)}
  .contact{position:absolute;left:282px;top:75px;font-family:"Arimo",sans-serif;color:var(--ink)}
  .contact__name{font-size:20px;font-weight:700}
  .contact__addr{font-size:14px;margin-top:2px}
  .contact__phone{display:flex;align-items:center;gap:8px;font-size:19px;margin-top:24px}
  .band-line{position:absolute;left:0;right:0;top:244px;height:5px;background:var(--green-bright)}
  .band{position:absolute;left:0;right:0;top:252px;bottom:0;background:linear-gradient(90deg,var(--orange),var(--amber) 55%,var(--yellow))}
  .web{position:absolute;left:28px;bottom:17px;font-family:"Arimo",sans-serif;font-size:13px;color:#fff}

  /* appointment */
  .appt__title{position:absolute;left:36px;top:52px;font-family:"Cinzel",serif;font-weight:500;font-size:18px;color:var(--green);letter-spacing:.5px}
  .appt__row{position:absolute;left:36px;font-size:14.5px;color:#333;display:flex;align-items:flex-end}
  .rule{display:inline-block;border-bottom:1px solid #555;height:1px;margin:0 6px 5px}
  .rule--dots{border-bottom:1px dotted #555}
  .box{display:inline-block;width:96px;height:20px;border:1px solid #555;margin-left:10px}
  .days{position:absolute;left:32px;top:207px;display:flex;align-items:center;font-weight:700;font-size:14.5px;color:#555}
  .days .box{width:34px;margin:0 12px 0 6px}
  .note{position:absolute;left:32px;top:256px;width:470px;font-size:12.5px;color:#333;line-height:1.35}
  .card--appt-a .brand{right:52px;top:20px;width:110px}
  .card--appt-a .brand__dot{width:36px;height:36px}
  .card--appt-a .brand__name{font-size:8px;margin-top:5px}
  .faint-name{position:absolute;left:110px;top:218px;width:360px;text-align:center;font-family:"Open Sans",sans-serif;font-weight:600;font-size:40px;letter-spacing:6px;color:var(--faint)}

  /* back */
  .card--back .brand{left:0;right:0;top:34px;margin:0 auto;width:300px}
  .card--back .brand__name{font-size:20px;letter-spacing:3px}
  .back__web{position:absolute;left:0;right:0;top:208px;text-align:center;font-size:13px;letter-spacing:2.4px;color:var(--ink)}
  .back__hours-title{position:absolute;left:0;right:0;top:238px;text-align:center;font-weight:700;font-size:18px;letter-spacing:1.5px;color:#5a5a5a}
  .back__hours{position:absolute;left:0;right:0;top:273px;text-align:center;font-weight:600;font-size:14.5px;color:#5a5a5a}
  .back__hours span{margin:0 8px;color:#999;font-weight:400}
</style>
</head>
<body>
<main class="canvas">

  <section class="card card--front">
    <div class="brand">
      <div class="brand__dot"></div>
      <div class="brand__name">Velmo<br>Body Sugaring</div>
    </div>
    <div class="divider"></div>
    <div class="contact">
      <div class="contact__name">Fern by Dew by Lenka</div>
      <div class="contact__addr">14 Korrin Sqr 3942 Talloway</div>
      <div class="contact__phone">
        <svg width="16" height="16" viewBox="0 0 16 16" aria-hidden="true"><circle cx="8" cy="8" r="7" fill="none" stroke="#f39a1f" stroke-width="1.6"/><path d="M5.5 4.5c.6-.5 1.1-.3 1.4.3l.5 1c.2.4 0 .8-.3 1l-.4.3c.4.9 1 1.5 1.9 2l.3-.4c.3-.3.6-.4 1-.2l1 .5c.6.3.7.9.2 1.4-.9.9-2.5.6-4-.9s-2.5-3.5-1.6-5z" fill="#e9572a"/></svg>
        03 9481 2267
      </div>
    </div>
    <div class="band-line"></div>
    <div class="band"></div>
    <div class="web">www.FernAndDewByLenka.com.au</div>
  </section>

  <section class="card card--appt-a">
    <div class="brand">
      <div class="brand__dot"></div>
      <div class="brand__name">Velmo Body Sugaring</div>
    </div>
    <h2 class="appt__title">YOUR APPOINTMENT</h2>
    <div class="appt__row" style="top:92px">Name :<span class="rule rule--dots" style="width:290px"></span></div>
    <div class="appt__row" style="top:131px">Date :<span class="rule" style="width:96px;margin-left:20px"></span>Time :<span class="rule" style="width:92px"></span>am / pm</div>
    <div class="appt__row" style="top:169px">Next Appointment<span class="box"></span><span class="box" style="margin-left:28px"></span></div>
    <div class="days">MON<span class="box"></span>TUE<span class="box"></span>WED<span class="box"></span>THU<span class="box"></span>FRI<span class="box"></span>SAT<span class="box"></span></div>
    <p class="note">It would be appreciated if 24 hours notice could be given if you are unable to attend an appointment</p>
  </section>

  <section class="card card--back">
    <div class="brand">
      <div class="brand__dot" style="width:80px;height:80px"></div>
      <div class="brand__name">Velmo<br>Body Sugaring</div>
    </div>
    <div class="back__web">www.FernAndDewByLenka.com.au</div>
    <div class="back__hours-title">Hours of Operation</div>
    <div class="back__hours">Mon - Fri: 7.30am - 7.00pm<span>|</span>Saturday: 7.30am - 12.00pm</div>
  </section>

  <section class="card card--appt-b">
    <div class="faint-name" aria-hidden="true">VELMO</div>
    <h2 class="appt__title">YOUR APPOINTMENT</h2>
    <div class="appt__row" style="top:92px">Name :<span class="rule rule--dots" style="width:290px"></span></div>
    <div class="appt__row" style="top:131px">Date :<span class="rule" style="width:96px;margin-left:20px"></span>Time :<span class="rule" style="width:92px"></span>am / pm</div>
    <div class="appt__row" style="top:169px">Next Appointment<span class="box"></span><span class="box" style="margin-left:28px"></span></div>
    <div class="days">MON<span class="box"></span>TUE<span class="box"></span>WED<span class="box"></span>THU<span class="box"></span>FRI<span class="box"></span>SAT<span class="box"></span></div>
    <p class="note">It would be appreciated if 24 hours notice could be given if you are unable to attend an appointment</p>
  </section>

</main>
</body>
</html>
```